Commercial, Public Works, Contractor needs a modern web design

We are a General and Engineering contracting firm with vast experience in our industry. Our focus is on Commercial, Tenant Improvement, Restaurants, and Public Works. We are opening a new business and would like that excitement and energy to show through the new web design. The colors we like are black, red and grey, we are open to color ideas. Attached is our logo design.

Industry/Entity Type

Restaurant

```html
<!DOCTYPE html>
<html lang="en">
<head>
<meta charset="utf-8">
<title>Halden Contracting — General Contractor</title>
<link href="https://fonts.googleapis.com/css2?family=Open+Sans:wght@400;600&display=swap" rel="stylesheet">
<style>
:root{
  --red:#b5141b;
  --ink:#222;
  --text:#333;
  --muted:#8a8a8a;
  --line:#e2e2e2;
  --footer:#272727;
  --footer-bottom:#1e1e1e;
  --footer-text:#b9b9b9;
  --white:#fff;
}
*{box-sizing:border-box;margin:0;padding:0}
html,body{width:763px;height:1200px;overflow:hidden;background:var(--white)}
body{position:relative;font-family:"Open Sans",Arial,sans-serif;color:var(--text)}

/* header */
.site-header{position:absolute;left:0;top:0;width:763px;height:63px;background:var(--white);border-bottom:1px solid var(--line)}
.brand{position:absolute;left:56px;top:23px;display:flex;align-items:center;gap:7px;font-size:13px;font-weight:400;color:var(--ink)}
.brand-mark{width:10px;height:10px;background:var(--red)}
.main-nav a{position:absolute;top:25px;font-size:11px;color:var(--text);text-decoration:none}
.main-nav a.active{color:var(--red)}
.nav-caret{position:absolute;left:243px;top:42px}

/* hero */
.hero{position:absolute;left:0;top:63px;width:763px;height:305px;background:linear-gradient(135deg,#8a929c 0%,#a8adb3 40%,#7d858e 70%,#bfc3c7 100%)}
.hero h1{position:absolute;left:0;top:89px;width:763px;text-align:center;color:var(--white);font-size:33px;font-weight:600;line-height:39px}
.hero-arrow{position:absolute;top:148px;width:11px;height:11px;border-radius:50%;border:1px solid rgba(255,255,255,.7)}

/* welcome */
.welcome h2{position:absolute;left:0;top:389px;width:763px;text-align:center;font-size:18px;font-weight:400;color:var(--ink)}
.welcome p{position:absolute;left:120px;top:419px;width:523px;text-align:center;font-size:9px;line-height:17.6px;color:var(--muted)}
.btn-outline{position:absolute;left:333px;top:490px;width:98px;height:25px;border:1px solid var(--red);color:var(--red);font-size:9px;line-height:23px;text-align:center}

/* services */
.services{position:absolute;left:0;top:546px;width:763px;height:198px;background:linear-gradient(180deg,#3c4454 0%,#565d69 55%,#8a8f98 100%)}
.services h2{position:absolute;left:0;top:22px;width:763px;text-align:center;font-size:17px;font-weight:400;color:var(--white)}
.service-card{position:absolute;top:58px;width:155px}
.service-photo{height:88px}
.service-label{height:28px;background:var(--red);color:var(--white);font-size:9.5px;line-height:28px;text-align:center}
.band-shadow{position:absolute;left:0;top:744px;width:763px;height:14px;background:radial-gradient(ellipse at top,rgba(0,0,0,.18),rgba(0,0,0,0) 70%)}

/* blog */
.blog h2{position:absolute;left:0;top:764px;width:763px;text-align:center;font-size:17px;font-weight:400;color:var(--ink)}
.post-photo{position:absolute;width:128px;height:66px;border:3px solid var(--white);box-shadow:0 0 2px rgba(0,0,0,.25)}
.post-title{position:absolute;font-size:10.5px;color:var(--red);letter-spacing:.2px}
.post-text{position:absolute;width:165px;font-size:7px;line-height:13.5px;color:var(--muted);text-align:justify}

/* newsletter */
.newsletter{position:absolute;left:56px;top:899px;width:652px;height:65px;border:1px solid var(--line)}
.newsletter h3{position:absolute;left:16px;top:10px;font-size:19px;font-weight:400;color:var(--red)}
.newsletter p{position:absolute;left:16px;top:35px;font-size:11.5px;color:var(--text)}
.email-field{position:absolute;left:351px;top:21px;width:178px;height:26px;border:1px solid var(--line);font-size:6.5px;color:#aaa;line-height:24px;padding-left:11px}
.btn-solid{position:absolute;left:553px;top:21px;width:79px;height:26px;background:var(--red);border-radius:2px;color:var(--white);font-size:11px;line-height:26px;text-align:center}

/* footer */
.site-footer{position:absolute;left:0;top:994px;width:763px;height:168px;background:var(--footer)}
.footer-title{position:absolute;top:17px;font-size:11px;color:var(--white);letter-spacing:.3px}
.footer-text{position:absolute;font-size:7.5px;line-height:14.4px;color:var(--footer-text)}
.footer-text .hl{color:var(--red)}
.news-thumb{position:absolute;left:249px;width:39px;height:28px}
.social{position:absolute;top:1116px;width:20px;height:20px;border-radius:50%;background:var(--red)}
.footer-bottom{position:absolute;left:0;top:1162px;width:763px;height:38px;background:var(--footer-bottom);border-top:1px solid #333}
.footer-bottom p{text-align:center;font-size:7.5px;color:#ddd;line-height:36px}
</style>
</head>
<body>

<header class="site-header">
  <div class="brand"><span class="brand-mark"></span>Halden Contracting</div>
  <nav class="main-nav">
    <a class="active" style="left:234px">Home</a>
    <a style="left:294px">About Us</a>
    <a style="left:368px">Services</a>
    <a style="left:437px">Company</a>
    <a style="left:513px">Latest News</a>
    <a style="left:601px">Blog</a>
    <a style="left:653px">Contact</a>
  </nav>
  <svg class="nav-caret" width="10" height="7" viewBox="0 0 10 7"><path d="M1 1l4 4 4-4" fill="none" stroke="#b5141b" stroke-width="2"/></svg>
</header>

<section class="hero" role="img" aria-label="Two engineers in hard hats reviewing plans in front of office towers">
  <span class="hero-arrow" style="left:56px"></span>
  <span class="hero-arrow" style="left:693px"></span>
  <h1>We Are Professional,<br>Competitive And<br>Competent In Our Service</h1>
</section>

<section class="welcome">
  <h2>Welcome to Halden Contracting</h2>
  <p>Sed ut perspiciatis unde omnis iste natus error sit voluptatem accusantium doloremque laudantium, totam rem aperiam, eaque ipsa quae ab illo inventore veritatis et quasi architecto beatae vitae dicta sunt explicaboSed ut perspiciatis unde omnis iste natus error sit&nbsp; illo inventore veritatis et quasi architecto beatae vitae dicta sunt explicabo</p>
  <div class="btn-outline">Learn More</div>
</section>

<section class="services" role="region" aria-label="Our services">
  <h2>Our Servies</h2>
  <div class="service-card" style="left:52px">
    <div class="service-photo" role="img" aria-label="Glass skyscrapers against a blue sky" style="background:linear-gradient(160deg,#5d8fc9,#2b4f7e 60%,#1b2c44)"></div>
    <div class="service-label">COMMERCIAL</div>
  </div>
  <div class="service-card" style="left:218px">
    <div class="service-photo" role="img" aria-label="Man sketching colourful planning ideas on a whiteboard" style="background:linear-gradient(135deg,#f2f2f2,#d9d9d9 60%,#bfc4c9)"></div>
    <div class="service-label">TENANT IMPROVEMENT</div>
  </div>
  <div class="service-card" style="left:384px">
    <div class="service-photo" role="img" aria-label="Modern restaurant dining room with warm lighting" style="background:linear-gradient(180deg,#6d3a22,#a8683e 50%,#d9c6b0)"></div>
    <div class="service-label">RESTAURANTS</div>
  </div>
  <div class="service-card" style="left:549px">
    <div class="service-photo" role="img" aria-label="Worker in safety vest at an industrial pipeline site" style="background:linear-gradient(160deg,#dfe6ec,#b6bfc4 55%,#8f8a78)"></div>
    <div class="service-label">PUBLIC WORKS</div>
  </div>
</section>
<div class="band-shadow"></div>

<section class="blog">
  <h2>From the Blog</h2>
  <div class="post-photo" role="img" aria-label="Construction team reviewing blueprints" style="left:57px;top:800px;background:linear-gradient(135deg,#e8edf2,#aebfd0 50%,#6f8aa6)"></div>
  <div class="post-title" style="left:206px;top:796px">PRAESENT VESTIBULUM SED</div>
  <div class="post-text" style="left:206px;top:818px">Lorem ipsum dolor sit amet, conse adipiscing elit. Praesent vestibulum molestie lacus. Aenean nonummy hendrerit mauris,penatibus et magnis dis.</div>

  <div class="post-photo" role="img" aria-label="Engineer drawing plans at a desk" style="left:392px;top:800px;background:linear-gradient(135deg,#f4f6f8,#c9d2da 55%,#8a9aa9)"></div>
  <div class="post-title" style="left:540px;top:796px">PRAESENT VESTIBULUM SED</div>
  <div class="post-text" style="left:540px;top:818px">Lorem ipsum dolor sit amet, conse adipiscing elit. Praesent vestibulum molestie lacus. Aenean nonummy hendrerit mauris,penatibus et magnis dis.</div>
</section>

<section class="newsletter">
  <h3>Newsletter</h3>
  <p>Ut wisi enim ad minim veniam quis nostrud exerci tation</p>
  <div class="email-field">Enter your Email here.....</div>
  <div class="btn-solid">Get Updates</div>
</section>

<footer class="site-footer">
  <div class="footer-title" style="left:58px">ABOUT US</div>
  <div class="footer-text" style="left:57px;top:38px;width:123px;text-align:justify">Lorem ipsum dolor sit amet, onsectetuer adipiscing elit, sed diam nonummy nibh euismod tincidunt ut laoreet dolore magna</div>

  <div class="footer-title" style="left:249px">RECENT NEWS</div>
  <div class="news-thumb" role="img" aria-label="Workers silhouetted against a sunset" style="top:44px;background:linear-gradient(180deg,#e07a2a,#6b2a14)"></div>
  <div class="footer-text" style="left:296px;top:40px;width:90px">Sed diam nonummy nibh euismod tincidunt ut laoreet <span class="hl">19 Dec 2014</span></div>
  <div class="news-thumb" role="img" aria-label="Team in hard hats on a building site" style="top:95px;background:linear-gradient(180deg,#c9dbe8,#7f9a6a)"></div>
  <div class="footer-text" style="left:296px;top:92px;width:90px">Sed diam nonummy nibh euismod tincidunt ut laoreet <span class="hl">19 Jan 2015</span></div>
  <div class="footer-text" style="left:296px;top:139px;color:#ddd">[ MORE ]</div>

  <div class="footer-title" style="left:444px">USEFUL LINKS</div>
  <div class="footer-text" style="left:444px;top:34px">Home<br>Services<br>Our Company<br>Latest News<br>Blog<br>Contact Us</div>

  <div class="footer-title" style="left:589px">CONTACT INFO</div>
  <div class="footer-text" style="left:589px;top:34px;width:120px">Pellentesque nec erat,Aenean emper neque non faucibus.<br>Phone: <span class="hl">012.666.999</span><br>Fax: <span class="hl">012.666.999</span><br>Mail: <span class="hl">info@example.com</span></div>
</footer>
<span class="social" style="left:588px"></span>
<span class="social" style="left:614px"></span>
<span class="social" style="left:640px"></span>
<span class="social" style="left:665px"></span>

<div class="footer-bottom"><p>Copyright © 2014 . All Rights Reserved.</p></div>

</body>
</html>
```